Creation of brand identity and website "Tandem K"

I am currently seeking an brand, identity and web design for a new project called Tandem K. This is a brand new concept from scratch and you have free-reign on the whole design process, taking into account my preference below.

Must include the name "Tandem K", or "Tandem K: Or the year I woke Up". Kudos is this forms part of the brands logo

Design that can be easily scaled to potentially include: a blog, timeline and vlogs.

Minimal but effective use of colour (however any colours and combinations permitted

Use of icons/graphics over text wherever possible

Minimal use of frames and borders

I appreciate this is a fairly wide scope so please contact me on marblefinch@postwillow.com with any questions or more information on what the project is.

Target Market(s)

Male and Female 20-40
Blog readers
Selfhelp

Industry/Entity Type

Seeking

Number of Pages Required

1 page

Font styles to use
Serif
Sans Serif

Requirements
Must have
• It is in effect a blog design, so about me section, recent blog / archived posts, reader comments / Q and A section.
• A coded design would be appreciated to make my life easier however I have left the design as uncoded as getting the right design matters more to me and I want to keep the project open to as many designers as possible
Nice to have
• See project description for other details and please ask if you need anything else :)
Should not have
• Mustn't be cluttered or feel fussy
• Promote icons over text
• Frames / multiple borders

```html
<!DOCTYPE html>
<html lang="en">
<head>
<meta charset="utf-8">
<title>Tandem K: Or the year I woke Up</title>
<link rel="stylesheet" href="https://fonts.googleapis.com/css2?family=Cinzel:wght@400;700&family=Lato:wght@400;700&family=Open+Sans:wght@700&display=swap">
<style>
:root{
  --green:#7f9e0b;
  --green-dark:#6c880a;
  --ink:#2b2b2b;
  --text:#3a3a3a;
  --muted:#777;
  --line:#dcdcdc;
  --white:#fff;
  --footer:#262626;
  --fb:#3b5998;
  --gp:#d9544a;
  --tw:#39a9e0;
  --li:#2a77b0;
  --em:#444;
}
*{box-sizing:border-box;margin:0;padding:0}
html,body{width:1200px;height:3340px;overflow:hidden;background:var(--white);font-family:"Lato",Arial,sans-serif;color:var(--text)}
.page{position:relative;width:1200px;height:3340px}

/* top strip */
.top-strip{position:absolute;left:0;top:0;width:1200px;height:44px;background:var(--green)}
.social{position:absolute;right:22px;top:11px;display:flex;gap:12px}
.social span{width:22px;height:22px;border-radius:50%;background:rgba(255,255,255,.85)}

/* header */
.masthead{position:absolute;left:0;top:44px;width:1200px;height:125px;text-align:center}
.brand{position:absolute;left:0;width:1200px;top:26px;font-family:"Cinzel",Georgia,serif;font-size:31px;font-weight:700;color:var(--ink);letter-spacing:.5px}
.brand b{color:var(--green);font-weight:700}
.main-nav{position:absolute;left:0;width:1200px;top:84px;display:flex;justify-content:center;gap:0;font-family:"Cinzel",Georgia,serif;font-size:17px;letter-spacing:1.5px}
.main-nav a{color:var(--ink);text-decoration:none;padding:0 26px;border-left:1px solid var(--line);line-height:20px}
.main-nav a:first-child{border-left:0}
.main-nav a.current{color:var(--green);position:relative}
.main-nav a.current::after{content:"";position:absolute;left:26px;right:26px;bottom:-10px;height:2px;background:var(--green)}

/* hero */
.hero{position:absolute;left:0;top:169px;width:1200px;height:400px;background:linear-gradient(90deg,#8a6a1e 0%,#d9b04a 30%,#f2d98a 55%,#c98f2f 80%,#7d4a18 100%)}
.hero::after{content:"";position:absolute;left:0;right:0;bottom:0;height:70px;background:linear-gradient(180deg,rgba(90,55,20,0),#5a3712)}
.hero-line{position:absolute;left:0;width:1060px;text-align:center;font-family:"Open Sans",Arial,sans-serif;font-weight:700;font-size:29px;color:var(--white);text-shadow:0 2px 4px rgba(0,0,0,.45);z-index:1}
.hero-line.one{top:164px}
.hero-line.two{top:204px}
.hero-arrow{position:absolute;top:190px;width:20px;height:30px;background:rgba(255,255,255,.35);z-index:1}
.hero-arrow.prev{left:0}
.hero-arrow.next{right:0}

/* categories */
.categories{position:absolute;left:0;top:569px;width:1200px;height:151px;display:flex}
.category{flex:1;display:flex;align-items:center;justify-content:center;gap:24px;background:var(--green);font-family:"Cinzel",Georgia,serif;font-size:24px;color:var(--white);letter-spacing:1px}
.category.active{background:var(--ink);color:var(--green)}
.category svg{width:92px;height:92px}

/* posts */
.posts{position:absolute;left:93px;top:783px;width:615px}
.post{position:relative;height:487px}
.post-date{position:absolute;left:0;top:0;width:63px;height:62px;background:var(--green);color:var(--white);font-size:36px;text-align:center;line-height:62px}
.post-month{position:absolute;left:0;top:80px;width:63px;text-align:right;font-size:13px;font-weight:700;color:var(--ink);line-height:18px}
.post-meta{position:absolute;left:0;width:63px;text-align:right;font-size:11px;line-height:15px;color:var(--ink)}
.post-meta span{display:block;color:var(--muted)}
.post-meta.by{top:136px}
.post-meta.cat{top:180px}
.share-toggle{position:absolute;left:4px;top:227px;width:56px;height:52px;background:var(--ink);display:flex;align-items:center;justify-content:center}
.post-frame{position:absolute;left:81px;top:0;width:534px;height:263px;border:1px solid var(--line);padding:10px}
.post-photo{width:100%;height:100%}
.post-title{position:absolute;left:81px;top:305px;width:534px;font-family:"Cinzel",Georgia,serif;font-weight:700;font-size:15px;letter-spacing:.6px;color:var(--ink)}
.post-excerpt{position:absolute;left:81px;top:330px;width:534px;font-size:13px;line-height:19px;color:var(--text)}
.post-rule{position:absolute;left:81px;top:383px;width:534px;height:1px;background:var(--line)}
.counters{position:absolute;left:81px;top:400px;display:flex;gap:20px}
.counter{width:38px;text-align:center}
.counter .count{display:block;height:25px;border:1px solid currentColor;font-size:11px;line-height:23px;background:var(--white)}
.counter .label{display:block;margin-top:3px;height:14px;background:#e9e9e9;font-size:9px;line-height:14px;color:var(--ink)}
.counter.fb{color:var(--fb)}.counter.gp{color:var(--gp)}.counter.tw{color:var(--tw)}.counter.li{color:var(--li)}.counter.em{color:var(--em)}
.read-more{position:absolute;display:block;width:107px;height:32px;background:var(--green);border:1px solid var(--green-dark);color:var(--white);font-size:13px;font-weight:700;text-align:center;line-height:30px;text-decoration:none;letter-spacing:.3px}
.post .read-more{left:508px;top:412px}

.load-more{position:absolute;left:80px;top:3221px;width:628px;height:40px;background:var(--green);color:var(--white);font-size:14px;font-weight:700;display:flex;align-items:center;justify-content:center;gap:10px}
.load-more i{width:16px;height:16px;border-radius:50%;background:rgba(255,255,255,.8)}

/* sidebar */
.widget-title{font-family:"Cinzel",Georgia,serif;font-size:25px;color:var(--ink);letter-spacing:.5px}
.widget-title b{color:var(--green);font-weight:400}
.about{position:absolute;left:777px;top:776px;width:343px}
.about-photo{position:absolute;left:0;top:50px;width:343px;height:160px;background:linear-gradient(90deg,#5d7482,#9fb0b8 45%,#d9d4cc 60%,#6f8794)}
.about-text{position:absolute;left:0;top:234px;width:343px;font-size:13px;line-height:19px}
.about .read-more{left:0;top:419px;height:34px}

.box{position:absolute;left:777px;width:343px;border:1px solid var(--line);padding:0 26px}
.box .widget-title{margin-top:20px}
.newsletter{top:1260px;height:232px}
.field{display:block;width:287px;height:31px;border:1px solid var(--line);margin-top:9px;font-size:11px;color:var(--muted);padding-left:8px;line-height:29px}
.newsletter .field:first-of-type{margin-top:12px}
.submit{position:absolute;left:176px;top:185px;width:111px;height:31px;background:var(--green);color:var(--white);font-size:13px;font-weight:700;text-align:center;line-height:31px}

.tags{top:1527px;height:220px}
.tag-list{display:grid;grid-template-columns:repeat(3,auto);gap:10px 6px;margin-top:14px;justify-content:start}
.tag{background:var(--green);color:var(--white);font-size:12px;font-weight:700;height:27px;line-height:27px;padding:0 8px;text-align:center}

.recent{top:1781px;height:283px}
.recent-add{position:absolute;right:26px;top:36px;width:28px;height:12px;background:var(--green)}
.recent-list{margin-top:10px}
.recent-item{display:flex;gap:14px;height:60px;margin-top:14px}
.recent-date{width:58px;flex:none}
.recent-date .m{display:block;height:30px;background:var(--green);color:var(--white);font-size:12px;text-align:center;line-height:30px}
.recent-date .d{display:block;height:30px;background:var(--ink);color:var(--white);font-size:13px;text-align:center;line-height:30px}
.recent-item h4{font-size:12px;font-weight:700;color:var(--ink);line-height:16px}
.recent-item p{font-size:11px;line-height:15px}

.weather{top:2097px;height:178px}
.forecast{display:flex;margin-top:14px;width:282px}
.day{flex:1;height:94px;color:var(--white);text-align:center;padding-top:6px}
.day small{display:block;font-size:10px;font-weight:700}
.day svg{width:34px;height:34px;margin-top:4px}
.day strong{display:block;font-size:25px;font-weight:400;line-height:26px}
.day.mon{background:#f6b447}.day.tue{background:#f19a4f}.day.wed{background:#3c9bd9}.day.thu{background:#2db27d}

.archives{top:2306px;height:287px}
.archives .widget-title{padding-bottom:12px;border-bottom:1px solid var(--line)}
.archive-list{list-style:none;margin-top:6px}
.archive-list li{font-size:13px;height:31px;line-height:31px;color:var(--ink)}

.ad{position:absolute;left:777px;top:2629px;width:343px;height:632px;background:linear-gradient(180deg,#d31f2b 0%,#c41623 60%,#a50f1b 100%)}
.ad-bottle{position:absolute;left:110px;top:30px;width:123px;height:470px;background:linear-gradient(180deg,#8e0d14,#e23a32 40%,#b3151e)}
.ad-line{position:absolute;left:0;width:343px;text-align:center;font-family:"Open Sans",Arial,sans-serif;font-weight:700;font-size:29px;color:var(--white)}
.ad-line.one{top:535px}.ad-line.two{top:570px}

.footer{position:absolute;left:0;top:3294px;width:1200px;height:46px;background:var(--footer);color:#cfcfcf;font-size:12px;text-align:center;line-height:46px}
</style>
</head>
<body>
<div class="page">

  <div class="top-strip">
    <div class="social" aria-label="Social links"><span></span><span></span><span></span><span></span></div>
  </div>

  <header class="masthead">
    <div class="brand">Tandem K: Or the Year <b>I Woke Up</b></div>
    <nav class="main-nav">
      <a class="current" href="#">About Me</a>
      <a href="#">Recent Blog</a>
      <a href="#">Reader Comments</a>
      <a href="#">Contact Us</a>
    </nav>
  </header>

  <section class="hero" role="img" aria-label="Woman with long hair sitting on a wooden bench, looking over a golden sunlit lake">
    <span class="hero-arrow prev"></span>
    <div class="hero-line one">A Different Kind of Company.</div>
    <div class="hero-line two">A Different Kind of Year I Woke Up</div>
    <span class="hero-arrow next"></span>
  </section>

  <section class="categories">
    <div class="category">
      <svg viewBox="0 0 92 92" aria-hidden="true"><path d="M46 30c-8-8-30-6-30 16 0 20 14 36 22 36 4 0 5-2 8-2s4 2 8 2c8 0 22-16 22-36 0-22-22-24-30-16z" fill="#fff"/><path d="M46 30c0-8 4-14 10-18" stroke="#fff" stroke-width="4" fill="none"/><path d="M50 22c6-8 16-8 18-6-4 6-12 8-18 6z" fill="#fff"/></svg>
      Nutrition
    </div>
    <div class="category active">
      <svg viewBox="0 0 92 92" aria-hidden="true"><circle cx="46" cy="46" r="44" fill="#7f9e0b"/><circle cx="46" cy="24" r="8" fill="#2b2b2b"/><path d="M34 38h24l4 22H30z" fill="#2b2b2b"/><path d="M34 40l-12 16 8 2M58 40l12 16-8 2" stroke="#2b2b2b" stroke-width="5" fill="none" stroke-linecap="round"/><path d="M18 66c10-8 46-8 56 0l-6 8H24z" fill="#2b2b2b"/></svg>
      Exercise
    </div>
    <div class="category">
      <svg viewBox="0 0 92 92" aria-hidden="true"><circle cx="22" cy="66" r="16" stroke="#fff" stroke-width="5" fill="none"/><circle cx="70" cy="66" r="16" stroke="#fff" stroke-width="5" fill="none"/><circle cx="56" cy="14" r="8" fill="#fff"/><path d="M22 66l16-24 14 10 18 14M38 42l14-14 10 12h10" stroke="#fff" stroke-width="6" fill="none" stroke-linejoin="round" stroke-linecap="round"/></svg>
      Sports
    </div>
  </section>

  <main class="posts">
    <article class="post">
      <div class="post-date">02</div>
      <div class="post-month">JULY<br>2016</div>
      <div class="post-meta by">POSTED BY<span>Admin</span></div>
      <div class="post-meta cat">CATEGORY<span>Terms</span></div>
      <div class="share-toggle"><svg width="26" height="26" viewBox="0 0 26 26" aria-hidden="true"><circle cx="19" cy="5" r="4" fill="#fff"/><circle cx="6" cy="13" r="4" fill="#fff"/><circle cx="19" cy="21" r="4" fill="#fff"/><path d="M19 5L6 13l13 8" stroke="#fff" stroke-width="2" fill="none"/></svg></div>
      <div class="post-frame"><div class="post-photo" role="img" aria-label="Three people meditating on yoga mats in a bright studio" style="background:linear-gradient(90deg,#e9e4de,#d7c3a8 60%,#b98d5e)"></div></div>
      <h3 class="post-title">Lorem Ipsum Dolor Sit Amet Consectetuer Adipiscing</h3>
      <p class="post-excerpt">Lorem ipsum dolor sit amet, consectetuer adipiscing elit, sed diam nonummy nibh euismod tincidunt ut laoreet dolore magna aliquam erat volutpat. Ut wisi enim ad</p>
      <div class="post-rule"></div>
      <div class="counters">
        <div class="counter fb"><span class="count">560</span><span class="label">Like</span></div>
        <div class="counter gp"><span class="count">236</span><span class="label">+1</span></div>
        <div class="counter tw"><span class="count">456</span><span class="label">Post</span></div>
        <div class="counter li"><span class="count">366</span><span class="label">Share</span></div>
        <div class="counter em"><span class="count">1066</span><span class="label">Email</span></div>
      </div>
      <a class="read-more" href="#">READ MORE</a>
    </article>

    <article class="post">
      <div class="post-date">02</div>
      <div class="post-month">JULY<br>2016</div>
      <div class="post-meta by">POSTED BY<span>Admin</span></div>
      <div class="post-meta cat">CATEGORY<span>Terms</span></div>
      <div class="share-toggle"><svg width="26" height="26" viewBox="0 0 26 26" aria-hidden="true"><circle cx="19" cy="5" r="4" fill="#fff"/><circle cx="6" cy="13" r="4" fill="#fff"/><circle cx="19" cy="21" r="4" fill="#fff"/><path d="M19 5L6 13l13 8" stroke="#fff" stroke-width="2" fill="none"/></svg></div>
      <div class="post-frame"><div class="post-photo" role="img" aria-label="Mother and two children playing together on a sunny lawn" style="background:linear-gradient(160deg,#9ccc4a,#5f9a25 55%,#3f6e18)"></div></div>
      <h3 class="post-title">Lorem Ipsum Dolor Sit Amet Consectetuer Adipiscing</h3>
      <p class="post-excerpt">Lorem ipsum dolor sit amet, consectetuer adipiscing elit, sed diam nonummy nibh euismod tincidunt ut laoreet dolore magna aliquam erat volutpat. Ut wisi enim ad</p>
      <div class="post-rule"></div>
      <div class="counters">
        <div class="counter fb"><span class="count">560</span><span class="label">Like</span></div>
        <div class="counter gp"><span class="count">236</span><span class="label">+1</span></div>
        <div class="counter tw"><span class="count">456</span><span class="label">Post</span></div>
        <div class="counter li"><span class="count">366</span><span class="label">Share</span></div>
        <div class="counter em"><span class="count">1066</span><span class="label">Email</span></div>
      </div>
      <a class="read-more" href="#">READ MORE</a>
    </article>

    <article class="post">
      <div class="post-date">02</div>
      <div class="post-month">JULY<br>2016</div>
      <div class="post-meta by">POSTED BY<span>Admin</span></div>
      <div class="post-meta cat">CATEGORY<span>Terms</span></div>
      <div class="share-toggle"><svg width="26" height="26" viewBox="0 0 26 26" aria-hidden="true"><circle cx="19" cy="5" r="4" fill="#fff"/><circle cx="6" cy="13" r="4" fill="#fff"/><circle cx="19" cy="21" r="4" fill="#fff"/><path d="M19 5L6 13l13 8" stroke="#fff" stroke-width="2" fill="none"/></svg></div>
      <div class="post-frame"><div class="post-photo" role="img" aria-label="Two people doing sit-ups on the grass in a park" style="background:linear-gradient(180deg,#b8d86a,#7cb832 50%,#5e9a22)"></div></div>
      <h3 class="post-title">Lorem Ipsum Dolor Sit Amet Consectetuer Adipiscing</h3>
      <p class="post-excerpt">Lorem ipsum dolor sit amet, consectetuer adipiscing elit, sed diam nonummy nibh euismod tincidunt ut laoreet dolore magna aliquam erat volutpat. Ut wisi enim ad</p>
      <div class="post-rule"></div>
      <div class="counters">
        <div class="counter fb"><span class="count">560</span><span class="label">Like</span></div>
        <div class="counter gp"><span class="count">236</span><span class="label">+1</span></div>
        <div class="counter tw"><span class="count">456</span><span class="label">Post</span></div>
        <div class="counter li"><span class="count">366</span><span class="label">Share</span></div>
        <div class="counter em"><span class="count">1066</span><span class="label">Email</span></div>
      </div>
      <a class="read-more" href="#">READ MORE</a>
    </article>

    <article class="post">
      <div class="post-date">02</div>
      <div class="post-month">JULY<br>2016</div>
      <div class="post-meta by">POSTED BY<span>Admin</span></div>
      <div class="post-meta cat">CATEGORY<span>Terms</span></div>
      <div class="share-toggle"><svg width="26" height="26" viewBox="0 0 26 26" aria-hidden="true"><circle cx="19" cy="5" r="4" fill="#fff"/><circle cx="6" cy="13" r="4" fill="#fff"/><circle cx="19" cy="21" r="4" fill="#fff"/><path d="M19 5L6 13l13 8" stroke="#fff" stroke-width="2" fill="none"/></svg></div>
      <div class="post-frame"><div class="post-photo" role="img" aria-label="Man leaning over a pool table lining up a shot" style="background:linear-gradient(180deg,#2a211c 0%,#3d2f27 45%,#2f8fb8 70%,#3aa6cf)"></div></div>
      <h3 class="post-title">Lorem Ipsum Dolor Sit Amet Consectetuer Adipiscing</h3>
      <p class="post-excerpt">Lorem ipsum dolor sit amet, consectetuer adipiscing elit, sed diam nonummy nibh euismod tincidunt ut laoreet dolore magna aliquam erat volutpat. Ut wisi enim ad</p>
      <div class="post-rule"></div>
      <div class="counters">
        <div class="counter fb"><span class="count">560</span><span class="label">Like</span></div>
        <div class="counter gp"><span class="count">236</span><span class="label">+1</span></div>
        <div class="counter tw"><span class="count">456</span><span class="label">Post</span></div>
        <div class="counter li"><span class="count">366</span><span class="label">Share</span></div>
        <div class="counter em"><span class="count">1066</span><span class="label">Email</span></div>
      </div>
      <a class="read-more" href="#">READ MORE</a>
    </article>

    <article class="post">
      <div class="post-date">02</div>
      <div class="post-month">JULY<br>2016</div>
      <div class="post-meta by">POSTED BY<span>Admin</span></div>
      <div class="post-meta cat">CATEGORY<span>Terms</span></div>
      <div class="share-toggle"><svg width="26" height="26" viewBox="0 0 26 26" aria-hidden="true"><circle cx="19" cy="5" r="4" fill="#fff"/><circle cx="6" cy="13" r="4" fill="#fff"/><circle cx="19" cy="21" r="4" fill="#fff"/><path d="M19 5L6 13l13 8" stroke="#fff" stroke-width="2" fill="none"/></svg></div>
      <div class="post-frame"><div class="post-photo" role="img" aria-label="Smiling couple taking a photo together on a cliff above the sea" style="background:linear-gradient(90deg,#8a6a4c,#c49a78 40%,#4f86b8 70%,#6a8f4a)"></div></div>
      <h3 class="post-title">Lorem Ipsum Dolor Sit Amet Consectetuer Adipiscing</h3>
      <p class="post-excerpt">Lorem ipsum dolor sit amet, consectetuer adipiscing elit, sed diam nonummy nibh euismod tincidunt ut laoreet dolore magna aliquam erat volutpat. Ut wisi enim ad</p>
      <div class="post-rule"></div>
      <div class="counters">
        <div class="counter fb"><span class="count">560</span><span class="label">Like</span></div>
        <div class="counter gp"><span class="count">236</span><span class="label">+1</span></div>
        <div class="counter tw"><span class="count">456</span><span class="label">Post</span></div>
        <div class="counter li"><span class="count">366</span><span class="label">Share</span></div>
        <div class="counter em"><span class="count">1066</span><span class="label">Email</span></div>
      </div>
      <a class="read-more" href="#">READ MORE</a>
    </article>
  </main>

  <div class="load-more"><i></i>Load More Blogs</div>

  <aside>
    <section class="about">
      <h2 class="widget-title">About <b>Me</b></h2>
      <div class="about-photo" role="img" aria-label="Portrait of a smiling businesswoman in front of a glass office building"></div>
      <p class="about-text">Lorem ipsum dolor sit amet, consectetuer adipiscing elit, sed diam nonummy nibh euismod aliquet dime tincidunt ut laoreet dolore magna aliquam erat volutpat. Ut wisi enim ad minim veniam, quis dol nostrud exerci tation ullamcorper suscipit lobortis nisl ut aliquip ex ea commodo consequat lisl Duis autem vel eum iriure dolor in hendrerit in vulputate velit esse molestie consequat, vel alm illum dolore eu feugiat nulla facilis.</p>
      <a class="read-more" href="#">READ MORE</a>
    </section>

    <section class="box newsletter">
      <h2 class="widget-title">News Letter <b>Sign Up</b></h2>
      <span class="field">Name</span>
      <span class="field">Email</span>
      <span class="field">Phone</span>
      <span class="submit">SUBMIT</span>
    </section>

    <section class="box tags">
      <h2 class="widget-title">Tags</h2>
      <div class="tag-list">
        <span class="tag">EUROPE</span><span class="tag">AUSTRALIA</span><span class="tag">CANADA</span>
        <span class="tag">NEW ZEALAND</span><span class="tag">CARIBBEAN</span><span class="tag">ASIA</span>
        <span class="tag">UK</span><span class="tag">SOUTH PACIFIC</span><span class="tag">AFRICA</span>
        <span class="tag">MEXICO</span><span class="tag">MIDDLE EAST</span><span class="tag">CANADA</span>
      </div>
    </section>

    <section class="box recent">
      <h2 class="widget-title">Recent <b>Posts</b></h2>
      <span class="recent-add"></span>
      <div class="recent-list">
        <div class="recent-item"><div class="recent-date"><span class="m">July</span><span class="d">02</span></div><div><h4>Lorem ipsum dolor sit amet ipsu</h4><p>Lorem ipsum dolor sit amet, ectetuer adipiscing elit, sed diam nonummy nibh</p></div></div>
        <div class="recent-item"><div class="recent-date"><span class="m">July</span><span class="d">01</span></div><div><h4>Lorem ipsum dolor sit amet ipsu</h4><p>Lorem ipsum dolor sit amet, ectetuer adipiscing elit, sed diam nonummy nibh</p></div></div>
        <div class="recent-item"><div class="recent-date"><span class="m">June</span><span class="d">30</span></div><div><h4>Lorem ipsum dolor sit amet ipsu</h4><p>Lorem ipsum dolor sit amet, ectetuer adipiscing elit, sed diam nonummy nibh</p></div></div>
      </div>
    </section>

    <section class="box weather">
      <h2 class="widget-title">Weather</h2>
      <div class="forecast">
        <div class="day mon"><small>MON</small><svg viewBox="0 0 34 34" aria-hidden="true"><circle cx="17" cy="17" r="7" fill="none" stroke="#fff" stroke-width="2"/><path d="M17 2v5M17 27v5M2 17h5M27 17h5M6 6l4 4M24 24l4 4M6 28l4-4M24 10l4-4" stroke="#fff" stroke-width="2"/></svg><strong>32°</strong></div>
        <div class="day tue"><small>TUE</small><svg viewBox="0 0 34 34" aria-hidden="true"><path d="M9 24a8 8 0 0 1 16 0" fill="none" stroke="#fff" stroke-width="2"/><path d="M3 27h28M17 6v6M6 13l4 4M28 13l-4 4" stroke="#fff" stroke-width="2"/></svg><strong>16°</strong></div>
        <div class="day wed"><small>WED</small><svg viewBox="0 0 34 34" aria-hidden="true"><path d="M9 20a6 6 0 0 1 2-11 8 8 0 0 1 15 2 5 5 0 0 1-1 9z" fill="none" stroke="#fff" stroke-width="2"/><path d="M12 24l-2 5M18 24l-2 5M24 24l-2 5" stroke="#fff" stroke-width="2"/></svg><strong>10°</strong></div>
        <div class="day thu"><small>THU</small><svg viewBox="0 0 34 34" aria-hidden="true"><path d="M20 5a12 12 0 1 0 10 17A10 10 0 0 1 20 5z" fill="none" stroke="#fff" stroke-width="2"/></svg><strong>7°</strong></div>
      </div>
    </section>

    <section class="box archives">
      <h2 class="widget-title">Archives</h2>
      <ul class="archive-list">
        <li>July 2016</li><li>June 2016</li><li>May 2016</li><li>April 2016</li><li>March 2016</li><li>February 2016</li><li>January 2016</li>
      </ul>
    </section>

    <section class="ad">
      <div class="ad-bottle" role="img" aria-label="Tall stack of sliced red tomatoes shaped like a ketchup bottle"></div>
      <div class="ad-line one">No One Grows</div>
      <div class="ad-line two">Ketchup Like Redvale.</div>
    </section>
  </aside>

  <footer class="footer">Copyright © 2016 Tandem K: Or the year I woke Up &nbsp;|&nbsp; All Rights Reserved.</footer>
</div>
</body>
</html>
```